Business Cards - Brightpath Horizon

need to design unique business card for my mortgage business. I need to design credit card style business card for my business or any unique idea that you might have

Target Market(s)

Home Loan customers

Industry/Entity Type

Mortgage Brokerage

Contact Information for Business Card

please design credit card style or very unique style business card

Colors

Designer to choose colors to be used in the design.

Requirements
Must have
• Name
• position
• Phone number
• fax number
• email address
• website address
• social media address
• All above fields will be provided once design in finalised

```html
<!DOCTYPE html>
<html lang="en">
<head>
<meta charset="utf-8">
<title>Brightpath Horizon – Business Cards</title>
<link href="https://fonts.googleapis.com/css2?family=Work+Sans:wght@400;500&display=swap" rel="stylesheet">
<style>
  :root {
    --backdrop-light: #2e2e2e;
    --backdrop-dark: #0d0d0d;
    --card: #262626;
    --card-edge: #1c1c1c;
    --silver: #a9a9a9;
    --brand-blue: #2f48b3;
    --name-blue: #1f5fc4;
    --accent-orange: #f0962a;
    --text-light: #f2f2f2;
  }
  * { margin: 0; padding: 0; box-sizing: border-box; }
  html, body { width: 1200px; height: 900px; overflow: hidden; }
  body {
    background: radial-gradient(ellipse at 60% 35%, var(--backdrop-light), var(--backdrop-dark) 75%);
    font-family: "Work Sans", Arial, sans-serif;
    position: relative;
  }
  .card {
    position: absolute;
    left: 290px;
    width: 620px;
    height: 354px;
    background: linear-gradient(160deg, #2d2d2d, var(--card) 55%, var(--card-edge));
    box-shadow: 0 18px 40px rgba(0,0,0,.6);
  }
  .card--front { top: 50px; }
  .card--back { top: 480px; }

  .wordmark {
    display: flex;
    align-items: center;
    gap: 14px;
    font-weight: 500;
    letter-spacing: 2px;
    text-transform: uppercase;
    line-height: 1.1;
  }
  .wordmark__square { width: 22px; height: 22px; flex: none; }

  .card--front .wordmark {
    position: absolute;
    left: 0; right: 0; top: 50%;
    transform: translateY(-50%);
    justify-content: center;
    font-size: 42px;
    color: var(--silver);
  }
  .card--front .wordmark__square { background: var(--silver); }

  .card--back .wordmark {
    position: absolute;
    left: 40px; top: 140px;
    width: 270px;
    font-size: 28px;
    color: var(--brand-blue);
  }
  .card--back .wordmark__square { background: var(--brand-blue); width: 18px; height: 18px; }

  .divider {
    position: absolute;
    left: 330px; top: 108px;
    width: 2px; height: 196px;
    background: var(--accent-orange);
  }
  .details {
    position: absolute;
    left: 360px; top: 112px;
    color: var(--text-light);
  }
  .details__name {
    font-size: 22px;
    font-weight: 500;
    letter-spacing: 1.5px;
    color: var(--name-blue);
    text-transform: uppercase;
  }
  .details__role { font-size: 15px; letter-spacing: 1px; margin-top: 2px; }
  .details__address { font-size: 15px; line-height: 1.35; margin-top: 14px; letter-spacing: .5px; }
  .contact-list { list-style: none; margin-top: 14px; }
  .contact-list li {
    display: flex; align-items: center; gap: 14px;
    font-size: 15px; letter-spacing: .5px; line-height: 1.6;
  }
  .contact-list svg { width: 14px; height: 14px; flex: none; fill: var(--name-blue); }
</style>
</head>
<body>

<section class="card card--front">
  <div class="wordmark"><span class="wordmark__square"></span><span>Brightpath<br>Horizon</span></div>
</section>

<section class="card card--back">
  <div class="wordmark"><span class="wordmark__square"></span><span>Brightpath<br>Horizon</span></div>
  <div class="divider"></div>
  <div class="details">
    <p class="details__name">Daniel Hart</p>
    <p class="details__role">FOUNDER</p>
    <p class="details__address">47 Lakeview Rd E,<br>Toronto ON M4K 2B6</p>
    <ul class="contact-list">
      <li>
        <svg viewBox="0 0 14 14" aria-hidden="true"><path d="M4 0h6a1 1 0 0 1 1 1v12a1 1 0 0 1-1 1H4a1 1 0 0 1-1-1V1a1 1 0 0 1 1-1zm0 2v9h6V2z"/></svg>
        (416) 555-0147
      </li>
      <li>
        <svg viewBox="0 0 14 14" aria-hidden="true"><path d="M3 0h8v4H3zM1 5h12a1 1 0 0 1 1 1v5h-3v3H3v-3H0V6a1 1 0 0 1 1-1zm3 5v3h6v-3z"/></svg>
        (416) 555-0193
      </li>
      <li>
        <svg viewBox="0 0 14 14" aria-hidden="true"><path d="M0 2h14v10H0zm1.5 1.2L7 7.5l5.5-4.3z"/></svg>
        d.hart@brightpathmail.net
      </li>
      <li>
        <svg viewBox="0 0 14 14" aria-hidden="true"><circle cx="7" cy="7" r="7"/><path d="M0 7h14M7 0c-3 3-3 11 0 14M7 0c3 3 3 11 0 14" stroke="#262626" stroke-width="1" fill="none"/></svg>
        brightpathhomes.com
      </li>
    </ul>
  </div>
</section>

</body>
</html>
```